Legal firm website redesign

Existing site for Sydney CBD lawyer needs clean and professional redesign - http://brintonlaw.com.au

The site will be viewed by a wide range of users: businesses, individuals, referral partners and other lawyers.

Please see the list of must haves for further details

Target Market(s)

Businesses, individuals, referral partners and other lawyers

Industry/Entity Type

Lawyer

Requirements
Must have
• Prominent display of phone number.
List of services down the left hand side of the site (5x services or so).
Search box in header.
Please use the greys and blues from the existing header.
New header must include the wording "Efficiency - Fulfillment - Integrity - Teamwork"

```html
<!DOCTYPE html>
<html lang="en">
<head>
<meta charset="utf-8">
<title>Brinton Law – Commercial Lawyers Sydney</title>
<link href="https://fonts.googleapis.com/css2?family=Arimo:wght@400;700&family=Open+Sans:wght@400;600&display=swap" rel="stylesheet">
<style>
:root{
  --ink:#1c1c1c;
  --brand-ink:#33383f;
  --header-grey:#aab1ba;
  --page-dark:#0c0f14;
  --page-blue:#4a8fd0;
  --page-grey:#5b6168;
  --nav-blue:#2f8fe3;
  --nav-blue-dark:#1769c0;
  --tab-dark:#1b1b1b;
  --hero-light:#eef2f6;
  --accent-blue:#3a8fd0;
  --footer-blue:#2c86d6;
  --footer-blue-deep:#0d3f7e;
  --footer-text:#e9f3ff;
  --footer-head:#1f3f66;
  --pill-border:#e6894a;
  --bottom-grey:#7e858e;
  --bottom-mark:#b9bdc2;
}
*{box-sizing:border-box;margin:0;padding:0}
html,body{width:1200px;height:1113px;overflow:hidden}
body{position:relative;font-family:"Arimo",Arial,sans-serif;color:var(--ink);
  background:linear-gradient(180deg,var(--page-dark) 123px,#1a2a40 240px,var(--page-blue) 450px,#8f959c 451px,var(--page-grey) 1113px)}
.topline{position:absolute;left:0;top:0;width:1200px;height:7px;background:#3a3d42}
.site-header{position:absolute;left:0;top:7px;width:1200px;height:116px;
  background:linear-gradient(180deg,#b8bec6,var(--header-grey) 60%,#9ea5ae);border-bottom:1px solid #c9ced5}
.brand{position:absolute;left:146px;top:56px;font-weight:700;font-size:34px;line-height:40px;color:var(--brand-ink)}
.header-photo{position:absolute;left:440px;top:2px;width:340px;height:108px;
  background:linear-gradient(90deg,rgba(170,177,186,0),#8c929a 25%,#7b8088 60%,rgba(170,177,186,0))}
.header-contact{position:absolute;left:791px;top:12px;font-size:16.5px;line-height:22px;color:#111}
.search{position:absolute;left:789px;top:79px;width:219px;height:27px;background:#f2f3f4;border:1px solid #c5c9ce}
.search span{position:absolute;left:10px;top:7px;font-size:10px;color:#9a9ea4}
.search .btn{position:absolute;right:0;top:0;width:26px;height:25px;background:#d9dcdf}
.container{position:absolute;left:132px;top:128px;width:885px}
.nav{position:absolute;left:0;top:0;width:885px;height:42px;
  background:linear-gradient(180deg,#5fb0f2,var(--nav-blue) 50%,var(--nav-blue-dark));border-bottom:2px solid #0f4f96}
.nav a{position:absolute;top:13px;font-size:13px;color:#fff;text-decoration:none}
.nav .active{left:6px;top:4px;width:82px;height:30px;line-height:30px;text-align:center;background:var(--tab-dark)}
.hero{position:absolute;left:0;top:42px;width:885px;height:367px;background:linear-gradient(180deg,#f5f8fb,var(--hero-light));
  box-shadow:0 6px 8px rgba(0,0,0,.35)}
.hero-photo{position:absolute;left:13px;top:60px;width:381px;height:274px;border-radius:6px;
  background:radial-gradient(circle at 30% 35%,#e88a2c,#b14a12 55%,#4a1d08)}
.hero-copy{position:absolute;left:401px;top:172px;width:484px;height:188px;background:linear-gradient(180deg,#c3d2df,#d9e4ee)}
.tagline{position:absolute;left:414px;top:132px;font-size:21px;color:var(--accent-blue)}
.hero-copy p{position:absolute;left:13px;width:415px;font-size:12.6px;line-height:13px;color:#222}
.arrow{position:absolute;width:36px;height:36px}
.about{position:absolute;left:0;top:409px;width:885px;height:190px;background:linear-gradient(180deg,#e8e9ea,#c9cacc)}
.about h2{position:absolute;left:25px;top:32px;font:400 20px "Open Sans",Arial,sans-serif}
.about p{position:absolute;left:25px;width:640px;font-size:12.6px;line-height:13px}
.pill{position:absolute;left:454px;top:147px;width:416px;height:34px;border:1px solid var(--pill-border);border-radius:7px;
  background:#eef0f2;font-size:15.5px;color:#7a7f85;line-height:32px;text-align:center}
.services{position:absolute;left:0;top:599px;width:885px;height:241px;
  background:linear-gradient(180deg,var(--footer-blue),#1e6cbc 55%,var(--footer-blue-deep));border-top:3px solid #5aaeef}
.services h3{position:absolute;top:34px;font-size:12.8px;font-weight:700;color:var(--footer-head)}
.services ul{position:absolute;list-style:none;font-size:10.5px;line-height:18.4px;color:var(--footer-text)}
.divider{position:absolute;top:60px;width:1px;height:150px;background:#a9cdf0}
.contact-block{position:absolute;left:707px;top:66px;color:#fff;font-weight:700;font-size:11.5px;line-height:18.5px}
.contact-block strong{display:block;font-size:16px;margin-bottom:2px}
.links{position:absolute;left:0;top:840px;width:885px;height:46px;background:#0d3f7e;border-top:1px solid #2a62a4}
.links p{position:absolute;left:13px;top:15px;font-size:13px;color:#6fb6f5}
.links .social{position:absolute;top:12px;width:21px;height:21px;border-radius:2px}
.bottom{position:absolute;left:0;top:886px;width:885px;height:94px;background:linear-gradient(180deg,#8c939b,var(--bottom-grey))}
.bottom .mark{position:absolute;left:18px;top:30px;font-weight:700;font-size:27px;color:var(--bottom-mark)}
.bottom .copy{position:absolute;left:218px;top:40px;font-size:13px;color:#f2f2f2}
</style>
</head>
<body>
<div class="topline"></div>
<header class="site-header">
  <div class="brand">brinton law</div>
  <div class="header-photo" role="img" aria-label="Photo of a handshake beside a judge's gavel"></div>
  <div class="header-contact">Telephone (02) 9400 2710<br>Facsimile (02) 9400 2720<br>Email info@brintonlaw.com.au</div>
  <div class="search"><span>Search our site</span>
    <div class="btn"><svg width="26" height="25" viewBox="0 0 26 25"><circle cx="12" cy="11" r="4" fill="none" stroke="#444" stroke-width="1.6"/><line x1="15" y1="14" x2="18" y2="17" stroke="#444" stroke-width="2"/></svg></div>
  </div>
</header>

<main class="container">
  <nav class="nav">
    <a class="active" href="#">Home</a>
    <a href="#" style="left:103px">About Us</a>
    <a href="#" style="left:173px">Areas of Law</a>
    <a href="#" style="left:269px">Publications</a>
    <a href="#" style="left:367px">Contact</a>
  </nav>

  <section class="hero">
    <div class="hero-photo" role="img" aria-label="Photo of a gavel and brass scales of justice in warm light"></div>
    <div class="tagline">Efficiency - Fulfillment - Integrity - Teamwork</div>
    <div class="hero-copy">
      <p style="top:14px">Brinton Law is a dynamic commercial law firm in the CBD of Sydney providing services to corporate, small business and private clients.</p>
      <p style="top:52px">Brinton Law brings together over 30 years of experience in legal practice.</p>
      <p style="top:78px">The strong focus of the firm is on commercial law and estate planning.</p>
      <p style="top:104px">Brinton Law is committed to providing quality legal services in helping its clients achieve their objectives by providing a proactive understanding of its clients' businesses and creative legal solutions.</p>
    </div>
    <svg class="arrow" style="left:23px;top:276px" viewBox="0 0 36 36"><circle cx="18" cy="18" r="18" fill="#2a8be0"/><path d="M21 11l-7 7 7 7" fill="none" stroke="#fff" stroke-width="3.5"/></svg>
    <svg class="arrow" style="left:820px;top:292px" viewBox="0 0 36 36"><circle cx="18" cy="18" r="18" fill="#2a8be0"/><path d="M15 11l7 7-7 7" fill="none" stroke="#fff" stroke-width="3.5"/></svg>
  </section>

  <section class="about">
    <h2>About Brinton Law</h2>
    <p style="top:69px">Brinton Law is a dynamic commercial law firm in the CBD of Sydney providing services to corporate, small business and private clients.</p>
    <p style="top:106px">Brinton Law brings together over 30 years of experience in legal practice.</p>
    <p style="top:133px">The strong focus of the firm is on commercial law and estate planning.</p>
    <div class="pill">Please feel free to contact us if you have any questions.</div>
  </section>

  <section class="services">
    <h3 style="left:29px">Commercial/Business Transactions</h3>
    <ul style="left:40px;top:69px">
      <li>Buying and selling businesses and companies</li><li>Financing</li><li>Leasing</li><li>Property transactions</li>
      <li>Joint ventures</li><li>Business restructuring</li><li>Contract review and advice</li><li>Employment Law Documentation, e.g. AWAs</li>
    </ul>
    <div class="divider" style="left:313px"></div>
    <h3 style="left:352px;top:38px">Buying and selling businesses and companies</h3>
    <ul style="left:360px;top:69px">
      <li>We have acted on many transactions including:</li>
      <li>• purchase and subsequent sale of an airline;</li><li>• sale of a medical waste recycling company;</li>
      <li>• purchase of an insurance brokerage;</li><li>• purchase of numerous rent rolls for real estate agents;</li>
      <li>• sale of a waste disposal company to a multi-national;</li><li>• sale of a hydraulic hose company to a multi-national;</li>
      <li>• sale of a significant motor vehicle dealership.</li><li>• purchase of a national air conditioning company</li>
    </ul>
    <div class="divider" style="left:686px;top:39px"></div>
    <h3 style="left:707px">Contact</h3>
    <div class="contact-block"><strong>BRINTON LAW</strong>Telephone (02) 9400 2710<br>Facsimile (02) 9400 2720<br>Email info@brintonlaw.com.au</div>
  </section>

  <footer class="links">
    <p>Home | About Us | Area of Law | Our People | Publication | Contact</p>
    <span class="social" style="left:766px;background:#6b7077"></span>
    <span class="social" style="left:795px;background:#2e6fc6"></span>
    <span class="social" style="left:824px;background:#2a84c4"></span>
    <span class="social" style="left:854px;background:#e57a26"></span>
  </footer>

  <div class="bottom">
    <div class="mark">brinton law</div>
    <div class="copy">BrintonLaw © 2012 &nbsp; I &nbsp; Privacy Policy</div>
  </div>
</main>
</body>
</html>
```